Automotive component supplier needs a business card design

We need a business card design for our company called Velran Global Components Ltd based in the UK. We are a supplier of interior and exterior components to premium car manufacturers such as Corvel Ashby, Hadley Fenn, Marquist and Tavarelli. We would like to see a modern business card design that uses the colour blue.

Target Market(s)

Premium automotive car manufacturers.

Industry/Entity Type

Automotive

Contact Information for Business Card

Company Name : Velran Global Components Limited
Address: 17 Marlow Yard, Upper Heath, Warwick, CV31 8QL, United Kingdom
Web Address : www.velrancomponents-example.co.uk

Font styles to use
Other font styles liked:
• Helvetica

Colors
3176b5
0255a3
85acd3
cfdeed
cee9f5
85cae6
34a6d7
0692cd
9bcb3c

Requirements
Must have
• Clear company logo and a mixture of blue colours.
Nice to have
• A high quality modern image.
Should not have
• Multiple colours.

```html
<!DOCTYPE html>
<html lang="en">
<head>
<meta charset="utf-8">
<title>Velran Global Components – Business Card</title>
<link rel="stylesheet" href="https://fonts.googleapis.com/css2?family=Montserrat:wght@400;500;600;700&display=swap">
<style>
  :root {
    --backdrop: #2a2a2c;
    --blue-light: #34a6d7;
    --blue-mid: #0692cd;
    --lime: #9bcb3c;
    --white: #ffffff;
    --card-radius: 22px;
  }
  * { box-sizing: border-box; margin: 0; padding: 0; }
  html, body {
    width: 1200px; height: 1000px; overflow: hidden;
    background: var(--backdrop);
    font-family: "Montserrat", Helvetica, Arial, sans-serif;
  }
  .card {
    position: absolute; left: 250px;
    width: 700px; height: 400px;
    border-radius: var(--card-radius);
    overflow: hidden;
    box-shadow: 0 18px 40px rgba(0,0,0,.45);
  }
  .brand {
    position: absolute; display: flex; align-items: center; gap: 12px;
    font-weight: 600; letter-spacing: 1px; white-space: nowrap;
  }
  .brand__dot { width: 14px; height: 14px; border-radius: 50%; background: var(--lime); flex: none; }

  /* Front */
  .card--front {
    top: 60px;
    background: linear-gradient(135deg, var(--blue-light) 0%, var(--blue-mid) 100%);
    color: var(--white);
  }
  .card--front .brand { left: 50%; top: 140px; transform: translateX(-50%); font-size: 32px; color: var(--white); }
  .card--front .legal-name {
    position: absolute; left: 0; right: 0; bottom: 70px; text-align: center;
    font-size: 18px; font-weight: 600; letter-spacing: 1.2px; text-transform: uppercase;
  }

  /* Back */
  .card--back { top: 540px; background: var(--white); }
  .card--back .bands { position: absolute; inset: 0; }
  .card--back .brand { left: 110px; top: 82px; font-size: 26px; color: var(--blue-light); }
  .person { position: absolute; left: 40px; top: 288px; }
  .person__name { font-size: 26px; font-weight: 700; color: var(--lime); letter-spacing: .5px; text-transform: uppercase; white-space: nowrap; }
  .person__role { font-size: 15px; color: var(--white); text-align: right; margin-top: 2px; }
  .divider { position: absolute; left: 372px; top: 215px; width: 1px; height: 150px; background: rgba(255,255,255,.75); }
  .contact { position: absolute; left: 390px; top: 200px; color: var(--white); font-size: 14px; line-height: 1.42; }
  .contact__address { margin-bottom: 6px; }
  .contact__row { display: flex; align-items: center; gap: 8px; white-space: nowrap; font-size: 12px; }
  .contact__icon { width: 12px; height: 12px; flex: none; }
</style>
</head>
<body>
  <section class="card card--front">
    <div class="brand"><span class="brand__dot"></span>VELRAN GLOBAL COMPONENTS</div>
    <p class="legal-name">Velran Global Components Limited</p>
  </section>

  <section class="card card--back">
    <svg class="bands" width="700" height="400" viewBox="0 0 700 400" aria-hidden="true">
      <defs>
        <linearGradient id="backBlue" x1="0" y1="0" x2="1" y2="1">
          <stop offset="0" stop-color="#34a6d7"/>
          <stop offset="1" stop-color="#0692cd"/>
        </linearGradient>
      </defs>
      <polygon points="0,258 700,122 700,400 0,400" fill="url(#backBlue)"/>
      <line x1="0" y1="256" x2="700" y2="120" stroke="#9bcb3c" stroke-width="5"/>
    </svg>

    <div class="brand"><span class="brand__dot"></span>VELRAN GLOBAL COMPONENTS</div>

    <div class="person">
      <p class="person__name">Lorin Ashcombe</p>
      <p class="person__role">Director</p>
    </div>

    <div class="divider"></div>

    <div class="contact">
      <p class="contact__address">17 Marlow Yard<br>Upper Heath, Warwick<br>CV31 8QL, United Kingdom</p>
      <p class="contact__row">
        <svg class="contact__icon" viewBox="0 0 12 12"><path d="M2 1l2 0 1 3-1.5 1a7 7 0 0 0 3.5 3.5L8 7l3 1v2a1 1 0 0 1-1 1A9 9 0 0 1 1 2a1 1 0 0 1 1-1z" fill="#9bcb3c"/></svg>
        +330 2417-5032
      </p>
      <p class="contact__row">
        <svg class="contact__icon" viewBox="0 0 12 12"><rect x="3" y="0.5" width="6" height="11" rx="1.2" fill="none" stroke="#9bcb3c" stroke-width="1.3"/><circle cx="6" cy="9.5" r=".8" fill="#9bcb3c"/></svg>
        +330 2493-6120
      </p>
      <p class="contact__row">
        <svg class="contact__icon" viewBox="0 0 12 12"><rect x="0.7" y="2.2" width="10.6" height="7.6" rx="1" fill="none" stroke="#9bcb3c" stroke-width="1.2"/><path d="M1 3l5 4 5-4" fill="none" stroke="#9bcb3c" stroke-width="1.2"/></svg>
        info@velrancomponents-example.co.uk
      </p>
      <p class="contact__row">
        <svg class="contact__icon" viewBox="0 0 12 12"><circle cx="6" cy="6" r="5" fill="none" stroke="#9bcb3c" stroke-width="1.2"/><path d="M1 6h10M6 1c-2.5 3-2.5 7 0 10M6 1c2.5 3 2.5 7 0 10" fill="none" stroke="#9bcb3c" stroke-width="1"/></svg>
        www.velrancomponents-example.co.uk
      </p>
    </div>
  </section>
</body>
</html>
```